Vortaleen - Lead the Way!

Vortaleen is a new Silicon Valley company, of the pimrela founders from Berlin, which provides a "Shared Hive Circle". This platform allows the crowd to support startups with money, experts and fame. Our Vision is, that everyone should become an entrepreneur.

Pls find all brief details in the attached document
Updates

Would be nice to have a list of more social services I'm available on, like a list of pictograms of all my services:

Find me on: chattro, fennwix+, qrt, mivrel, datebloom, pohk, rplex, etc...

pls make sure to use the right font:
http://www.typelarder-demo.com/fonts/Orbitron

Target Market(s)

Main target market is those already involved in the startup industry, by fundraising, investing, advising, cofounding and working. Vortaleen brings a totaly new transparency and collaborative way of starting companies to that business.

· Entrepreneurs (looking for funding, team and community)
· Investors (looking for hot investments and )
· Experts (workers looking for startups they can work for equity)
· Incubators & Business Schools (looking for tools to advise startups)

Industry/Entity Type

It Company

Requirements
Must have
• Pls find all brief details in the attached document
Nice to have

```html
<!DOCTYPE html>
<html lang="en">
<head>
<meta charset="utf-8">
<title>Vortaleen – Business Card</title>
<link href="https://fonts.googleapis.com/css2?family=Orbitron:wght@500&family=Questrial&family=Arimo:wght@400;700&display=swap" rel="stylesheet">
<style>
  :root {
    --stage: #393432;
    --paper: #ffffff;
    --brand-orange: #e4603b;
    --ink-grey: #5f5f5f;
    --ink-soft: #7a7a7a;
    --ink-dark: #2e2e2e;
    --paper-soft: #fbe4dc;
  }
  * { box-sizing: border-box; margin: 0; padding: 0; }
  html, body { width: 841px; height: 1200px; overflow: hidden; background: var(--stage); }
  .canvas { position: relative; width: 841px; height: 1200px; }

  .card { position: absolute; left: 101px; width: 644px; height: 374px; }
  .card--front { top: 196px; background: var(--paper); }
  .card--back { top: 664px; background: var(--brand-orange); }

  .edge-band { position: absolute; left: 77px; width: 489px; height: 11px; background: var(--brand-orange); }
  .edge-band--top { top: 0; }
  .edge-band--bottom { bottom: 0; }

  .brand { position: absolute; left: 58px; top: 100px; width: 190px; text-align: center; }
  .brand__mark { width: 150px; height: 96px; margin: 0 auto 14px; display: block; }
  .brand__name { font-family: "Orbitron", sans-serif; font-weight: 500; font-size: 29px; color: var(--ink-grey); line-height: 1; }
  .brand__tagline { font-family: "Questrial", sans-serif; font-size: 14px; color: var(--ink-dark); margin-top: 6px; padding-left: 22px; }

  .person { position: absolute; left: 286px; top: 104px; }
  .person__name { font-family: "Orbitron", sans-serif; font-weight: 500; font-size: 29px; letter-spacing: 0.5px; color: var(--brand-orange); line-height: 1; }
  .person__role { font-family: "Questrial", sans-serif; font-size: 18px; color: var(--ink-grey); margin-top: 11px; letter-spacing: 0.5px; }

  .contact { position: absolute; left: 286px; top: 212px; list-style: none; font-family: "Questrial", sans-serif; font-size: 14.5px; line-height: 16.5px; color: var(--ink-grey); }
  .contact__label { color: var(--brand-orange); }

  .social { position: absolute; left: 70px; top: 329px; display: flex; gap: 10px; list-style: none; font-family: "Questrial", sans-serif; font-size: 11px; color: var(--ink-soft); }
  .social__item { display: flex; align-items: center; gap: 7px; }
  .social__dot { width: 9px; height: 9px; background: #6c8fb3; display: inline-block; }

  .side-strip { position: absolute; top: 61px; width: 11px; height: 254px; background: var(--paper); }
  .side-strip--left { left: 0; }
  .side-strip--right { right: 0; }

  .pitch { position: absolute; left: 0; right: 0; top: 110px; text-align: center; font-family: "Arimo", sans-serif; color: var(--paper); }
  .pitch__question { font-weight: 700; font-size: 19px; }
  .pitch__invite { font-size: 18px; margin-top: 4px; }

  .divider { position: absolute; left: 119px; width: 403px; top: 288px; border-top: 1.5px dashed var(--paper-soft); }

  .offices { position: absolute; left: 0; right: 0; top: 307px; text-align: center; list-style: none; font-family: "Arimo", sans-serif; font-size: 11.5px; line-height: 16px; color: var(--paper-soft); }
</style>
</head>
<body>
<main class="canvas">
  <section class="card card--front" aria-label="Business card front">
    <div class="edge-band edge-band--top"></div>
    <div class="brand">
      <svg class="brand__mark" viewBox="0 0 150 96" aria-hidden="true"><circle cx="75" cy="48" r="40" fill="var(--brand-orange)"/></svg>
      <div class="brand__name">Vortaleen</div>
      <div class="brand__tagline">Lead the Way!</div>
    </div>
    <div class="person">
      <h1 class="person__name">MARTEN KOLBRAND</h1>
      <p class="person__role">FOUNDER AND CEO</p>
    </div>
    <ul class="contact">
      <li><span class="contact__label">website</span> www.vortaleen.com</li>
      <li><span class="contact__label">email</span> the@vortaleen.com</li>
      <li><span class="contact__label">phone</span> 081 555 204 318</li>
    </ul>
    <ul class="social">
      <li class="social__item"><span class="social__dot"></span>chirrup.com/martenkolbrand</li>
      <li class="social__item"><span class="social__dot"></span>facelink.com/martenkolbrand</li>
      <li class="social__item"><span class="social__dot"></span>proweb.in/martenkolbrand</li>
    </ul>
    <div class="edge-band edge-band--bottom"></div>
  </section>

  <section class="card card--back" aria-label="Business card back">
    <div class="side-strip side-strip--left"></div>
    <div class="side-strip side-strip--right"></div>
    <div class="pitch">
      <p class="pitch__question">Are you interested in Startups, Investments, Work?</p>
      <p class="pitch__invite">Join: Facelink.com/Vortaleen</p>
    </div>
    <div class="divider"></div>
    <ul class="offices">
      <li>Berlin - Lindenhof Strasse 14 . 10117 Berlin . Germany</li>
      <li>Silicon Valley - 218 Orchard Ln . Sunnyvale . CA 94086</li>
    </ul>
  </section>
</main>
</body>
</html>
```